Chimney Service company needs new business card design

We need a updated business card with our new logo added. We provide a full range of chimney services throughout Vermont and New Hampshire. The business card will be one sided and color. Attached is our current business card another document showing all the information we would like on the card.
We dont like a lot of flashy colors.... here is a link to our website to get an idea of our branding www.flueguardianvt.example

Target Market(s)

homeowners

Industry/Entity Type

Business

Contact Information for Business Card

See attached sheet for content.

Font styles to use
Serif
Sans Serif

Requirements
Must have
• all information provided on separate sheet
Should not have
• Additional information that may clogg up design

```html
<!DOCTYPE html>
<html lang="en">
<head>
<meta charset="utf-8">
<title>Flue Guardian – Business Card</title>
<link rel="stylesheet" href="https://fonts.googleapis.com/css2?family=Open+Sans:wght@400;700&display=swap">
<style>
  :root {
    --bg: #b9b9b9;
    --card-dark: #2b2b2b;
    --card-light: #f1f1f1;
    --card-light-edge: #dcdcdc;
    --brand-red: #a50d14;
    --ink: #2a2a2a;
    --ink-soft: #3a3a3a;
    --white: #ffffff;
  }
  * { box-sizing: border-box; margin: 0; padding: 0; }
  html, body { width: 1200px; height: 576px; overflow: hidden; }
  body { background: var(--bg); position: relative; font-family: "Open Sans", sans-serif; }

  .card {
    position: absolute;
    top: 138px;
    height: 292px;
    border-radius: 14px;
    overflow: hidden;
  }

  /* Back side */
  .card-back { left: 82px; width: 484px; background: var(--card-dark); }
  .card-back .brand {
    position: absolute; left: 0; right: 0; top: 118px;
    display: flex; align-items: center; justify-content: center; gap: 14px;
  }
  .card-back .brand-dot { width: 26px; height: 26px; border-radius: 50%; background: var(--brand-red); }
  .card-back .brand-name {
    font-weight: 400; font-size: 30px; letter-spacing: 1px; color: var(--white);
  }

  /* Front side */
  .card-front {
    left: 602px; width: 481px;
    background: linear-gradient(180deg, var(--card-light), var(--card-light-edge));
  }
  .card-front .header-band { position: absolute; left: 0; top: 0; width: 481px; height: 120px; }

  .tagline {
    position: absolute; right: 24px; top: 154px; top: 16px; text-align: right;
    color: var(--white); font-size: 12px; line-height: 16px;
  }

  .front-brand { position: absolute; left: 22px; top: 160px; top: 162px; display: flex; align-items: center; gap: 10px; }
  .front-brand { top: 160px; }
  .front-brand .brand-dot { width: 16px; height: 16px; border-radius: 50%; background: var(--brand-red); }
  .front-brand .brand-name { font-weight: 400; font-size: 24px; letter-spacing: 0.5px; color: var(--ink); }

  .service-area {
    position: absolute; right: 32px; top: 147px; text-align: right;
    font-weight: 700; font-size: 16px; line-height: 21px; color: var(--ink);
    text-transform: uppercase;
  }
  .since {
    display: flex; align-items: center; justify-content: flex-end; gap: 8px;
    font-weight: 400; font-size: 10px; line-height: 14px; margin-top: 4px;
  }
  .since .rule { width: 46px; height: 2px; background: var(--brand-red); }

  .services { position: absolute; left: 24px; top: 191px; list-style: none; }
  .services li {
    font-size: 13px; line-height: 16.8px; color: var(--ink-soft);
    display: flex; align-items: center; gap: 8px;
  }
  .services li::before {
    content: ""; width: 6px; height: 6px; border-radius: 50%; background: var(--brand-red);
  }

  .contacts { position: absolute; right: 18px; top: 218px; list-style: none; text-align: right; }
  .contacts li {
    font-size: 13px; line-height: 19.5px; color: var(--ink);
    display: flex; align-items: center; justify-content: flex-end; gap: 6px;
  }
  .contacts .accent { color: var(--brand-red); }
  .contacts svg { width: 11px; height: 11px; fill: var(--brand-red); }
</style>
</head>
<body>

  <section class="card card-back" aria-label="Card back">
    <div class="brand">
      <span class="brand-dot"></span>
      <span class="brand-name">Flue Guardian</span>
    </div>
  </section>

  <section class="card card-front" aria-label="Card front">
    <svg class="header-band" viewBox="0 0 481 120" aria-hidden="true">
      <path d="M0 0 H481 V78 Q240 40 0 88 Z" fill="var(--brand-red)"/>
      <path d="M0 96 Q240 50 481 86" stroke="var(--ink)" stroke-width="3" fill="none"/>
    </svg>

    <p class="tagline">Fully Insured &amp; Free Estimates «<br>Family Owned &amp; Operated «</p>

    <div class="front-brand">
      <span class="brand-dot"></span>
      <span class="brand-name">Flue Guardian</span>
    </div>

    <div class="service-area">
      Serving Valley and<br>North Counties
      <div class="since"><span class="rule"></span>SINCE 1994<span class="rule"></span></div>
    </div>

    <ul class="services">
      <li>Full Masonry Services</li>
      <li>Historic chimney restoration</li>
      <li>Stainless steel liners</li>
      <li>New Chimney installations</li>
      <li>Guild Certified Chimney sweeps</li>
    </ul>

    <ul class="contacts">
      <li>802-555-0147
        <svg viewBox="0 0 24 24" aria-hidden="true"><path d="M6.6 10.8a15 15 0 0 0 6.6 6.6l2.2-2.2a1 1 0 0 1 1-.25 11.4 11.4 0 0 0 3.6.57 1 1 0 0 1 1 1V20a1 1 0 0 1-1 1A17 17 0 0 1 3 4a1 1 0 0 1 1-1h3.5a1 1 0 0 1 1 1c0 1.25.2 2.45.57 3.57a1 1 0 0 1-.25 1z"/></svg>
      </li>
      <li>info@flueguardianvt.example
        <svg viewBox="0 0 24 24" aria-hidden="true"><path d="M2 5h20v14H2z M2 5l10 8 10-8" stroke="var(--white)" stroke-width="1.5"/></svg>
      </li>
      <li><span>www.<span class="accent">flueguardianvt</span>.example</span>
        <svg viewBox="0 0 24 24" aria-hidden="true"><circle cx="12" cy="12" r="10"/><path d="M2 12h20M12 2c3 3 3 17 0 20M12 2c-3 3-3 17 0 20" stroke="var(--white)" stroke-width="1.4" fill="none"/></svg>
      </li>
    </ul>
  </section>

</body>
</html>
```